Web design project for exciting Australian start-up

Background
We are looking for a creative and talented web design artist to work alongside our market leading web developer.
• You will be required to create a modern and clean design theme for our website, incorporating selected rustic colour scheme elements for our exciting Australian start-up to operate within the coffee industry.
reoccurring work to be expected to flow to the successful designer.
Requirements
• c. 5 - 10 page website
• Landing page
• Log in/ out
• 404 template
• Typography is emphasised
• Please use either a) typemarrow.com, b) free web fonts, c) brindle fonts
• All design elements in vector format
• Preferably with icons for each header title(i.e. about us, how it works etc) but designer have free reign over how the site looks, so might not be applicable
• All pages to be responsive
• Down to eSlab resolution

High level visual design brief attached - additional pages to be worked from base design.

Design inspiration
• We would like to use design elements from the following sources:
http://www.zandrix.com/halcyon/ (Functionality)
Colour scheme refer to logo and complementary style guide

```html
<!DOCTYPE html>
<html lang="en">
<head>
<meta charset="utf-8">
<title>Brewhaven – Australia's First Online Coffee Marketplace</title>
<link rel="stylesheet" href="https://fonts.googleapis.com/css2?family=Roboto:wght@300;400;500;700;900&display=swap">
<style>
  :root {
    --orange: #f7941d;
    --ink: #1d1d1d;
    --grey-text: #555555;
    --rule-grey: #b5b5b5;
    --icon-grey: #c9c9c9;
    --band: #f4f5f5;
    --white: #ffffff;
  }
  * { box-sizing: border-box; margin: 0; padding: 0; }
  html, body { width: 1200px; height: 910px; overflow: hidden; }
  body { font-family: "Roboto", sans-serif; background: var(--white); position: relative; color: var(--grey-text); }

  .site-header { position: absolute; left: 0; top: 0; width: 1200px; height: 106px; border-top: 3px solid var(--orange); background: var(--white); }
  .brand { position: absolute; left: 105px; top: 34px; display: flex; align-items: center; gap: 10px; }
  .brand-mark { width: 34px; height: 34px; border-radius: 50%; background: var(--orange); }
  .brand-name { font-weight: 900; font-size: 26px; letter-spacing: 2px; color: var(--ink); text-transform: uppercase; }
  .account-nav { position: absolute; left: 960px; top: 33px; display: flex; border: 1px solid #333; height: 31px; }
  .account-nav a { display: flex; align-items: center; justify-content: center; font-size: 14px; font-weight: 300; text-decoration: none; }
  .login { width: 77px; color: var(--orange); border-right: 1px solid #333; }
  .signup { width: 86px; color: var(--ink); }

  .hero { position: absolute; left: 0; top: 106px; width: 1200px; height: 496px; }
  .hero-photo { position: absolute; inset: 0;
    background: radial-gradient(ellipse 320px 260px at 420px 150px, #e9dccb 0%, #c9ad8c 35%, rgba(90,60,40,0) 75%),
                linear-gradient(90deg, #5a3f2e 0%, #6e5040 30%, #4a3022 55%, #2e1c12 75%, #6a625a 100%); }
  .hero-copy { position: absolute; left: 103px; top: 0; color: var(--white); font-weight: 300; }
  .hero-line { position: absolute; white-space: nowrap; font-size: 61px; line-height: 1; }
  .l1 { top: 84px; }
  .hero-rule { position: absolute; top: 156px; left: 0; width: 480px; height: 4px; background: var(--orange); }
  .l2 { top: 180px; }
  .l3 { top: 241px; }
  .learn-more { position: absolute; top: 308px; font-size: 31px; color: var(--orange); white-space: nowrap; text-decoration: none; font-weight: 300; }
  .watch-video { position: absolute; left: 1px; top: 358px; width: 190px; height: 49px; border: 2px solid var(--white); border-radius: 3px; display: flex; align-items: center; gap: 12px; padding-left: 13px; color: var(--white); font-weight: 500; font-size: 17px; text-decoration: none; white-space: nowrap; }

  .site-footer { position: absolute; left: 0; top: 602px; width: 1200px; height: 262px; }
  .footer-col { position: absolute; top: 20px; width: 200px; }
  .col-helpful { left: 124px; }
  .col-who { left: 384px; }
  .col-icon { height: 44px; display: block; }
  .col-helpful .col-icon { margin-left: 27px; }
  .col-who .col-icon { margin-left: 39px; }
  .col-title { font-size: 19px; font-weight: 300; color: var(--grey-text); margin-top: 14px; padding-bottom: 8px; border-bottom: 2px solid var(--rule-grey); width: 126px; white-space: nowrap; }
  .col-links { list-style: none; margin-top: 11px; }
  .col-links li { height: 30px; font-size: 15.5px; font-weight: 300; }
  .col-links a { color: var(--orange); text-decoration: none; }

  .connect-panel { position: absolute; left: 877px; top: 0; width: 323px; height: 262px; box-shadow: -6px 0 8px -6px rgba(0,0,0,0.25); }
  .connect-inner { position: absolute; left: 65px; top: 28px; }
  .connect-inner .col-icon { margin-left: 83px; height: 36px; }
  .social-list { display: flex; gap: 10px; margin-top: 18px; list-style: none; }
  .social-list li { width: 28px; height: 28px; border-radius: 50%; background: var(--orange); }
  .newsletter-title { font-size: 16px; font-weight: 300; color: var(--grey-text); margin-top: 20px; }
  .newsletter-form { display: flex; gap: 4px; margin-top: 8px; }
  .newsletter-form input { width: 153px; height: 23px; border: 1px solid #aaa; font: 300 10.5px "Roboto", sans-serif; padding-left: 10px; color: #888; }
  .newsletter-form button { width: 68px; height: 23px; border: none; background: var(--orange); color: var(--white); font: 400 11px "Roboto", sans-serif; border-radius: 2px; }

  .copyright-band { position: absolute; left: 0; top: 864px; width: 1200px; height: 46px; background: var(--band); border-top: 1px solid #e2e4e4; font-size: 11px; color: #444; padding: 16px 0 0 120px; }
</style>
</head>
<body>
  <header class="site-header">
    <div class="brand"><span class="brand-mark"></span><span class="brand-name">Brewhaven</span></div>
    <nav class="account-nav"><a class="login" href="#">Login</a><a class="signup" href="#">Sign Up</a></nav>
  </header>

  <section class="hero">
    <div class="hero-photo" role="img" aria-label="Steaming white cup of coffee beside a burlap sack spilling roasted coffee beans on a rustic wooden table"></div>
    <div class="hero-copy">
      <h1>
        <span class="hero-line l1">Australia’s</span>
        <span class="hero-rule"></span>
        <span class="hero-line l2">First Online</span>
        <span class="hero-line l3">Coffe Marketplace</span>
      </h1>
      <a class="learn-more" href="#">Learn More</a>
      <a class="watch-video" href="#">
        <svg width="32" height="32" viewBox="0 0 32 32" aria-hidden="true"><circle cx="16" cy="16" r="14.5" fill="none" stroke="#fff" stroke-width="2"/><path d="M13 10 L21 16 L13 22 Z" fill="#fff"/></svg>
        WATCH VIDEO
      </a>
    </div>
  </section>

  <footer class="site-footer">
    <div class="footer-col col-helpful">
      <svg class="col-icon" width="46" height="44" viewBox="0 0 46 44" aria-hidden="true">
        <rect x="2" y="16" width="6" height="12" fill="#c9c9c9"/>
        <path d="M9 16 L24 8 L24 36 L9 28 Z" fill="#c9c9c9"/>
        <path d="M28 16 Q32 22 28 28" fill="none" stroke="#c9c9c9" stroke-width="2"/>
        <path d="M32 12 Q39 22 32 32" fill="none" stroke="#c9c9c9" stroke-width="2"/>
      </svg>
      <h2 class="col-title">Helpful Info</h2>
      <ul class="col-links">
        <li><a href="#">About us</a></li>
        <li><a href="#">Media Enquiries</a></li>
        <li><a href="#">Terms &amp; Conditions</a></li>
        <li><a href="#">Privacy Policy</a></li>
      </ul>
    </div>
    <div class="footer-col col-who">
      <svg class="col-icon" width="44" height="44" viewBox="0 0 44 44" aria-hidden="true">
        <circle cx="22" cy="22" r="20" fill="none" stroke="#c9c9c9" stroke-width="2"/>
        <circle cx="22" cy="17" r="7" fill="#c9c9c9"/>
        <path d="M9 36 Q12 26 22 26 Q32 26 35 36 Q22 44 9 36 Z" fill="#c9c9c9"/>
      </svg>
      <h2 class="col-title">Who We Are</h2>
      <ul class="col-links">
        <li><a href="#">How it Works</a></li>
        <li><a href="#">FAQ</a></li>
        <li><a href="#">Contact Us</a></li>
      </ul>
    </div>

    <aside class="connect-panel">
      <div class="connect-inner">
        <svg class="col-icon" width="54" height="36" viewBox="0 0 54 36" aria-hidden="true">
          <g fill="none" stroke="#c9c9c9" stroke-width="2">
            <circle cx="11" cy="24" r="9"/><circle cx="43" cy="24" r="9"/>
            <path d="M11 24 L20 10 L36 10 L43 24 M20 10 L27 24 L36 10 M17 6 L23 6 M36 10 L34 4 L39 4"/>
          </g>
        </svg>
        <h2 class="col-title">Join Us On</h2>
        <ul class="social-list" aria-label="Social channels"><li></li><li></li><li></li><li></li></ul>
        <p class="newsletter-title">Newsletter</p>
        <form class="newsletter-form"><input type="email" placeholder="Your Email"><button type="button">Subscribe</button></form>
      </div>
    </aside>
  </footer>

  <div class="copyright-band">Copyright © 2014 Brewhaven</div>
</body>
</html>
```